BRELWINCare.co.uk - Mental Health Clinic for Child and Adolescents

Updated 29/01/2018***
I am not sure you guys are getting the idea regards to the opening page / homescreen layout. Can you look at the new images I have uploaded (page 5, 6 and 7) These are some of the layouts I like but to incorporate my chosen images, with the BRELWIN commissioner, buttons and a sliding header bar.
I have written a strong brief, I am looking for a website, preferably wordpress as i know they are easy to maintain. I am looking for a one page site, with the top / opening page being full screen image with drop down categories. I have made a rough design, see full brief in word doc attached, there is some freedom to play around with the design aspect but it will need to relay all the content provided. I like a minimal feel. I have also attached some images that may be useful, but will need a new logo for BRELWIN Care. I have attached some logo idea's, it is up to you decide whether you want to use them.
I would prefer the homepage as full screen image, and the categories offered as a drop down or over the main image.
I have also attached linked to some competitors websites:
https://www.vorimant-health.co.uk/
http://www.qlbn.org.uk/
Industry/Entity Type
Clinic
Number of Pages Required
1 page
Font styles to use
Look and feel
Each slider illustrates characteristics of the customer's brand and the style your logo design should communicate.

```html
<!DOCTYPE html>
<html lang="en">
<head>
<meta charset="utf-8">
<title>BRELWIN Care – Child &amp; Adolescent Mental Health</title>
<link href="https://fonts.googleapis.com/css2?family=Lato:wght@400;700;900&display=swap" rel="stylesheet">
<style>
:root{
  --white:#ffffff;
  --ink:#1d1d1d;
  --grey:#555a5e;
  --body-grey:#6b6f73;
  --sky:#1ab8ec;
  --teal:#19b0c6;
  --teal-bar:rgba(14,178,200,.85);
  --magenta:#e4047e;
  --plum:#7b2a7f;
  --lime:#9cc934;
  --yellow:#e8e62c;
  --blue-deep:#21499a;
  --blue-bright:#03b1d2;
  --brick:#ecebe9;
}
*{box-sizing:border-box;margin:0;padding:0}
html,body{width:1200px;height:2368px;overflow:hidden;background:var(--white)}
body{font-family:'Lato',sans-serif;color:var(--ink);position:relative}
a{color:inherit;text-decoration:none}

/* header */
.site-header{position:absolute;top:0;left:0;width:1200px;height:114px;background:var(--white);z-index:5}
.brand{position:absolute;left:120px;top:30px;display:flex;align-items:center;gap:12px}
.brand-dot{width:44px;height:44px;border-radius:50%;background:var(--yellow)}
.brand-name{font-weight:900;font-size:30px;color:var(--teal);letter-spacing:.5px}
.main-nav{position:absolute;left:366px;top:46px;display:flex;gap:18px;font-size:13.5px;font-weight:700;text-transform:uppercase}
.main-nav .active{color:var(--sky)}
.dropdown{position:absolute;left:360px;top:87px;width:202px;height:221px;background:var(--sky);padding:20px 18px 0 28px;z-index:6}
.dropdown::before{content:"";position:absolute;left:36px;top:-10px;border:10px solid transparent;border-top:0;border-bottom-color:var(--sky)}
.dropdown li{list-style:none;color:var(--white);font-size:13px;font-weight:700;text-transform:uppercase;height:37px;line-height:36px;border-bottom:1px solid rgba(255,255,255,.35)}
.dropdown li:last-child{border-bottom:0}

/* hero */
.hero{position:absolute;top:114px;left:0;width:1200px;height:571px;
  background:linear-gradient(100deg,#dcd4cb 0%,#c9b8a6 30%,#e9e4de 55%,#d8cabb 80%,#efece8 100%)}
.audience-btn{position:absolute;top:351px;width:300px;height:106px;border-radius:50%;display:flex;align-items:center;justify-content:center;color:var(--white);font-size:23px;font-weight:700;text-transform:uppercase}
.audience-btn::after{content:"";position:absolute;inset:9px 12px;border:2px solid var(--white);border-radius:50%}
.audience-btn.parents{left:286px;background:var(--plum)}
.audience-btn.commissioners{left:610px;background:var(--lime)}
.hero-bar{position:absolute;left:0;bottom:0;width:100%;height:77px;background:var(--teal-bar);display:flex;align-items:center;padding-left:123px;color:var(--white);font-size:22px;font-weight:700}
.hero-arrows{position:absolute;right:110px;top:24px;display:flex;gap:14px}

/* welcome */
.welcome{position:absolute;top:685px;left:0;width:1200px;height:420px}
.welcome-frame{position:absolute;left:160px;top:65px;width:887px;height:273px;border:2px solid var(--magenta);border-radius:56px}
.welcome-mark{position:absolute;left:574px;top:34px;width:58px;height:58px;border-radius:50%;background:var(--yellow);box-shadow:0 0 0 12px var(--white)}
.welcome h1{position:absolute;top:117px;width:100%;text-align:center;font-size:32px;font-weight:900;color:var(--grey)}
.welcome h1 span{color:var(--teal)}
.welcome p{position:absolute;left:225px;top:169px;width:750px;text-align:center;font-size:17px;line-height:31px;color:var(--body-grey)}
.pill{display:flex;align-items:center;justify-content:center;font-weight:700;text-transform:uppercase;border-radius:24px}
.welcome .pill{position:absolute;left:518px;top:309px;width:170px;height:48px;background:var(--magenta);color:var(--white);font-size:16px}

/* blogs */
.blogs{position:absolute;top:1105px;left:0;width:1200px;height:509px;background:linear-gradient(120deg,var(--blue-deep) 0%,#1d6bb0 45%,var(--blue-bright) 100%);color:var(--white)}
.blogs h2{position:absolute;top:47px;width:100%;text-align:center;font-size:31px;font-weight:700}
.blog-card{position:absolute;top:97px;width:300px;text-align:center}
.blog-photo{width:200px;height:200px;margin:8px auto 0;border-radius:50%;border:5px solid var(--yellow);box-shadow:inset 0 0 0 6px var(--white)}
.blog-card h3{margin-top:26px;font-size:20px;font-weight:700}
.blog-card p{font-size:14px;line-height:22px;margin:5px auto 0;width:270px}
.blog-card .pill{margin:16px auto 0;width:152px;height:45px;border:2px solid var(--white);font-size:14px}
.blogs .arrow{position:absolute;top:255px}

/* contact */
.contact{position:absolute;top:1614px;left:0;width:1200px;height:549px;background:var(--brick)}
.contact-frame{position:absolute;left:273px;top:72px;width:659px;height:300px;border:2px solid var(--magenta);border-bottom:0;border-radius:40px 40px 0 0}
.contact h2{position:absolute;top:50px;left:480px;width:246px;background:var(--brick);text-align:center;font-size:32px;font-weight:900;color:var(--magenta)}
.contact-details{position:absolute;top:110px;width:100%;text-align:center;list-style:none;font-size:17px;line-height:31px;color:var(--ink)}
.contact-photo{position:absolute;left:0;bottom:0;width:1200px;height:300px;background:linear-gradient(180deg,rgba(236,235,233,0) 0%,#c9b7a6 25%,#7b8d92 75%,#56797b 100%)}

/* footer */
.site-footer{position:absolute;top:2163px;left:0;width:1200px;height:205px;background:var(--plum);color:var(--white);text-align:center}
.footer-nav{display:flex;justify-content:center;gap:19px;margin-top:38px;font-size:17px;font-weight:700;text-transform:uppercase}
.copyright{margin-top:14px;font-size:15px}
.social{display:flex;justify-content:center;gap:8px;margin-top:20px}
.social span{width:43px;height:43px;border:2px solid var(--white);border-radius:50%}
</style>
</head>
<body>

<header class="site-header">
  <a class="brand" href="#"><span class="brand-dot"></span><span class="brand-name">BRELWIN</span></a>
  <nav class="main-nav">
    <a class="active" href="#">About Us</a>
    <a href="#">Our Team</a>
    <a href="#">Our Services</a>
    <a href="#">Blogs</a>
    <a href="#">Forum</a>
    <a href="#">Contact Us</a>
    <a href="#">Parents</a>
    <a href="#">Commisioners</a>
  </nav>
</header>
<ul class="dropdown">
  <li>What we do</li>
  <li>How we work</li>
  <li>Why we are</li>
  <li>Our mission</li>
  <li>Team</li>
</ul>

<section class="hero" role="img" aria-label="Photo of a therapist talking with a young boy in a bright room">
  <a class="audience-btn parents" href="#">Parents</a>
  <a class="audience-btn commissioners" href="#">Commisioners</a>
  <div class="hero-bar">ADHD and Austim Screening with 24 Hours
    <div class="hero-arrows">
      <svg width="20" height="30" viewBox="0 0 20 30"><polyline points="16,3 4,15 16,27" fill="none" stroke="#fff" stroke-width="3.5"/></svg>
      <svg width="20" height="30" viewBox="0 0 20 30"><polyline points="4,3 16,15 4,27" fill="none" stroke="#fff" stroke-width="3.5"/></svg>
    </div>
  </div>
</section>

<section class="welcome">
  <div class="welcome-frame"></div>
  <div class="welcome-mark"></div>
  <h1>WELCOME TO <span>BRELWIN</span></h1>
  <p>Vivamus porttitor purus nisi eleifend libero a tempus libero lectus feugiat felis Morbi diam mauris viverra in gravida eu mattis in ante Morbi eget arcu Morbi porta libero id ullamcorper nonummy nibh ligula pulvinar metus eget consectetuer augue nisi quis lacus Ut</p>
  <a class="pill" href="#">Read More</a>
</section>

<section class="blogs">
  <h2>OUR BLOGS</h2>
  <svg class="arrow" style="left:122px" width="24" height="40" viewBox="0 0 24 40"><polyline points="20,4 5,20 20,36" fill="none" stroke="#fff" stroke-width="4"/></svg>
  <article class="blog-card" style="left:140px;top:90px">
    <div class="blog-photo" role="img" aria-label="Photo of a girl talking on a sofa" style="background:linear-gradient(135deg,#e9e2d8,#b89a86)"></div>
    <h3>Aorta libero ullamcorper</h3>
    <p>nonummy nibh ligula pulvinar metus eget consectetuer augue nisi quis</p>
    <a class="pill" href="#">Read More</a>
  </article>
  <article class="blog-card" style="left:455px">
    <div class="blog-photo" role="img" aria-label="Photo of a smiling counsellor in a denim shirt" style="background:linear-gradient(135deg,#d9d2c8,#5d7ea4)"></div>
    <h3>Fusce ultricies orci</h3>
    <p>nonummy nibh ligula pulvinar metus eget consectetuer augue nisi quis</p>
    <a class="pill" href="#">Read More</a>
  </article>
  <article class="blog-card" style="left:770px">
    <div class="blog-photo" role="img" aria-label="Photo of a teenage boy sitting by a bookshelf" style="background:linear-gradient(135deg,#cfd2cc,#7b4a47)"></div>
    <h3>Nulla rhoncus dictu</h3>
    <p>nonummy nibh ligula pulvinar metus eget consectetuer augue nisi quis</p>
    <a class="pill" href="#">Read More</a>
  </article>
  <svg class="arrow" style="left:1070px" width="24" height="40" viewBox="0 0 24 40"><polyline points="4,4 19,20 4,36" fill="none" stroke="#fff" stroke-width="4"/></svg>
</section>

<section class="contact">
  <div class="contact-frame"></div>
  <div class="contact-photo" role="img" aria-label="Photo of five smiling teenagers sitting together on a sofa against a white brick wall"></div>
  <h2>CONTACT US</h2>
  <ul class="contact-details">
    <li>Phone Number: 0203 555 0188</li>
    <li>Address:&nbsp; Ashgrove Suite 2B, 44-52 Mill Lane, London, E17 4PL</li>
    <li>Opening Times: 9am – 5pm Mon-Fri</li>
    <li>Email: enquiry@brelwincare.co.uk</li>
  </ul>
</section>

<footer class="site-footer">
  <nav class="footer-nav">
    <a href="#">About Us</a>
    <a href="#">Our Team</a>
    <a href="#">Our Services</a>
    <a href="#">Blogs</a>
    <a href="#">Contact Us</a>
    <a href="#">Parents</a>
    <a href="#">Commisioners</a>
  </nav>
  <p class="copyright">© 2018 Company Name&nbsp; All right reserved</p>
  <div class="social">
    <span aria-label="Social link"></span>
    <span aria-label="Social link"></span>
    <span aria-label="Social link"></span>
    <span aria-label="Social link"></span>
  </div>
</footer>

</body>
</html>
```